Tech business card design

We need an amazing business card design for our new business 'Pexla' a marketing tech startup based in Sydney, Australia. We provide an online marketplace for businesses to search and buy advertising media, connect with service providers and learn more about marketing. We wish to communicate 'cool tech', reliability and professionalism and design based around our logo.

Target Market(s)

Business Owners

Contact Information for Business Card

Name
Position
Email Address
Website
Phone Number

Font styles to use
Other font styles liked:
• Avenir & Avenir Next

Colors

Designer to choose colors to be used in the design.

```html
<!DOCTYPE html>
<html lang="en">
<head>
<meta charset="utf-8">
<title>Pexla Business Card</title>
<link href="https://fonts.googleapis.com/css2?family=Nunito+Sans:wght@400;600;800;900&display=swap" rel="stylesheet">
<style>
  :root {
    --navy: #161640;
    --white: #ffffff;
    --stage: #e6e7ea;
    --ink-soft: #4a4a66;
    --divider: #2a2a5c;
  }
  * { box-sizing: border-box; margin: 0; padding: 0; }
  html, body { width: 1200px; height: 900px; overflow: hidden; }
  body {
    background: var(--stage);
    font-family: "Nunito Sans", "Avenir Next", Avenir, sans-serif;
    display: flex;
    flex-direction: column;
    align-items: center;
    justify-content: center;
    gap: 40px;
  }
  .card {
    width: 630px;
    height: 360px;
    position: relative;
    box-shadow: 0 10px 24px rgba(0,0,0,0.18);
  }
  .card--front { background: var(--white); border-bottom: 4px solid var(--navy); }
  .card--back { background: var(--navy); display: flex; align-items: center; justify-content: center; }

  .wordmark {
    font-weight: 900;
    letter-spacing: -2px;
    line-height: 1;
  }
  .card--front .wordmark {
    position: absolute;
    left: 56px;
    top: 142px;
    font-size: 84px;
    color: var(--navy);
  }
  .card--back .wordmark { font-size: 120px; color: var(--white); }

  .divider {
    position: absolute;
    left: 356px;
    top: 92px;
    width: 2px;
    height: 160px;
    background: var(--divider);
  }
  .contact {
    position: absolute;
    left: 382px;
    top: 88px;
    color: var(--ink-soft);
    font-size: 14px;
    line-height: 1.4;
  }
  .contact__name { font-size: 21px; font-weight: 800; color: var(--navy); line-height: 1.15; }
  .contact__role { font-size: 14px; margin-bottom: 12px; }
  .contact__address { margin-bottom: 10px; }
  .contact__line { display: flex; align-items: center; gap: 9px; }
  .contact__line svg { width: 11px; height: 11px; flex: none; }
</style>
</head>
<body>
  <section class="card card--front" aria-label="Card front">
    <div class="wordmark">Pexla</div>
    <div class="divider"></div>
    <div class="contact">
      <div class="contact__name">Daniel Reeve</div>
      <div class="contact__role">Director</div>
      <div class="contact__address">812 Alder Street<br>Brookvale, NC 27514</div>
      <div class="contact__line">
        <svg viewBox="0 0 12 12" aria-hidden="true"><path d="M2.5 1 L4.5 1 L5.2 3.6 L3.9 4.6 Q5 7 7.4 8.1 L8.4 6.8 L11 7.5 L11 9.5 Q10.5 11 9 11 Q1 10 1 2.5 Q1 1.2 2.5 1 Z" fill="#161640"/></svg>
        <span>+330 1875-3920</span>
      </div>
      <div class="contact__line">
        <svg viewBox="0 0 12 12" aria-hidden="true"><rect x="1" y="2.5" width="10" height="7" fill="none" stroke="#161640" stroke-width="1.2"/><path d="M1 2.5 L6 6.5 L11 2.5" fill="none" stroke="#161640" stroke-width="1.2"/></svg>
        <span>info@pexla.com</span>
      </div>
      <div class="contact__line">
        <svg viewBox="0 0 12 12" aria-hidden="true"><circle cx="6" cy="6" r="5" fill="none" stroke="#161640" stroke-width="1.1"/><ellipse cx="6" cy="6" rx="2.2" ry="5" fill="none" stroke="#161640" stroke-width="1"/><path d="M1 6 H11" stroke="#161640" stroke-width="1"/></svg>
        <span>www.pexla.com</span>
      </div>
    </div>
  </section>

  <section class="card card--back" aria-label="Card back">
    <div class="wordmark">Pexla</div>
  </section>
</body>
</html>
```